Im want a website LIKE VRX's and FleetHollow.com's with product payment options like Trenzo's

I need a website LIKE VRX with a header made EXACTLY LIKE THAT OF FLEETHOLLOWS .

The front page photo should be like that of FLEETHOLLOW's webpage as well.

The name of the website will be called "M.K. (Caldera Key)".

We will be targeting ALL MARKETS in a small town in central Panama and charging businesses "listing fees" like a phone book does but also providing informational blogs, news, and other interesting activities.

THIS IS A MULTI PAGE WEBSITE

THIS IS WHERE VRX's website meets Brivelle/FleetHollow.

Once the layout is built I will tweak and modify, add information, and upload items for sale.

Here is a list of specific categories that should be listed out above the front page header image/search bar

-- Home -- News -- Travel -- Activities -- Shop & Dine -- Store -- More... --

These categories should be spread across the bottom of the page in three sections:

WHATS SO GREAT ABOUT (Caldera Key),
HAND PICKED TOURS
ACTIVITIES etc.

Also lets use www.Trenzo.example 's
"HOT DESTINATIONS"
"BEAT THE BEST PRICES IN BOQUETE"
"OCTOBERS INSIDER PICKS"
"TOP DESTINATIONS"
and spread them in four sections side-by-side near the bottom of the page.

Overall I would like to see the finished product to be something LIKE VRX's and FleetHollows.

WE NEED ONLINE PAYMENT OPTIONS LIKE BRIVELLE'S WEBSITE HAS

This will be a desktop website but should be very mobile friendly as well.

-rodmund

P.S. Good luck!

If it isn't already too late to change the website name, the name of the website should be "Caldera Key". Added Friday, October 9, 2015

What do you guys think the budget should be to win this? Added Saturday, October 10, 2015

www.palmorra.example is the most amazing simple site. Whoever can make me a replica with my specifications will win immediately!!!! Added Sunday, October 18, 2015

OMG www.palmorra.example is the bomb!So simple and elegant. Whoever can make me an EXACT REPLICA OF WWW.PALMORRA.EXAMPLE as my site with the specifications mentioned in my brief will take home the $825.00 immediately! Good luck amigos! Added Sunday, October 18, 2015

Does anybody know how to add recurring monthly billing options on this website? Added Sunday, October 18, 2015

ALL MARKETS

Product

Coded - Design and coding required

5+ page

• Coinvey payment options.
• I must be able to add and remove photos/text and video from the HTML files in the page.
• Be creative my friends, and may the odds be forever in your favor!
• I added some photos of a good layout for our page below.

```html
<!DOCTYPE html>
<html lang="en">
<head>
<meta charset="utf-8">
<title>Caldera Key</title>
<link rel="stylesheet" href="https://fonts.googleapis.com/css2?family=Open+Sans:wght@300;400;600;700&family=Roboto+Condensed:wght@400;700&display=swap">
<style>
:root{
  --navy:#123a5e;
  --navy-dark:#0d2c49;
  --blue:#1f8bd3;
  --blue-light:#47a9e8;
  --accent:#2a8fd6;
  --orange:#f29a1f;
  --text:#555d66;
  --muted:#8a939c;
  --grey-bg:#eef0f2;
  --line:#dde1e5;
  --footer:#1c2530;
  --white:#ffffff;
}
*{box-sizing:border-box;margin:0;padding:0}
html,body{width:1200px;height:2328px;overflow:hidden}
body{font-family:'Open Sans',Arial,sans-serif;color:var(--text);background:var(--white);position:relative}
a{color:inherit;text-decoration:none}

/* top bar */
.topbar{height:88px;background:var(--navy);display:flex;align-items:center;justify-content:space-between;padding:0 64px}
.brand{display:flex;align-items:center;gap:14px;color:var(--white);font-size:30px;font-weight:700;letter-spacing:2px}
.brand-mark{width:14px;height:14px;background:var(--blue-light)}
.top-tools{display:flex;align-items:center;gap:12px}
.lang{display:flex;align-items:center;gap:8px;font-size:13px;color:#cfe0ef}
.lang-box{width:62px;height:22px;background:#dfe6ee;border-radius:2px}
.social{display:flex;gap:8px}
.social span{width:28px;height:28px;border-radius:50%;display:block}
.s1{background:#3b5a98}.s2{background:#2fb1e8}.s3{background:#d9473b}.s4{background:#0e76a8}.s5{background:#e8702a}

/* nav */
.mainnav{height:48px;background:var(--blue);display:flex;padding:0 64px}
.mainnav a{display:flex;align-items:center;padding:0 40px;color:var(--white);font-size:14px;font-weight:600;letter-spacing:1px}
.mainnav a.active{background:var(--blue-light)}

/* hero */
.hero{position:relative;height:504px;overflow:hidden}
.hero-photo{position:absolute;inset:0;background:linear-gradient(180deg,#1d2d4a 0%,#6a5a4e 28%,#e7a84a 48%,#f4c35a 56%,#b86a2f 72%,#2c2b2a 100%)}
.palm-left,.palm-right{position:absolute;top:0;bottom:0;width:130px}
.palm-left{left:0;background:linear-gradient(90deg,#1f4a2a,rgba(31,74,42,0))}
.palm-right{right:0;background:linear-gradient(270deg,#1f4a2a,rgba(31,74,42,0))}
.hero-content{position:relative;text-align:center;padding-top:128px;color:var(--white)}
.hero-title{font-size:66px;font-weight:700;letter-spacing:1px;text-shadow:0 2px 6px rgba(0,0,0,.35)}
.hero-sub{font-size:18px;margin-top:18px;text-shadow:0 1px 4px rgba(0,0,0,.5)}
.btn{display:inline-block;background:var(--blue);color:var(--white);font-size:16px;font-weight:600;padding:14px 34px;border-radius:3px;margin-top:84px}
.dots{position:absolute;bottom:42px;left:0;right:0;display:flex;justify-content:center;gap:10px}
.dots span{width:12px;height:12px;border-radius:50%;border:2px solid var(--white)}
.dots span.on{background:var(--white)}

/* sections */
.section-title{text-align:center;font-size:30px;font-weight:400;color:var(--accent);letter-spacing:1px}
.section-rule{width:70px;height:2px;background:var(--accent);margin:12px auto 0}
.intro{width:900px;margin:26px auto 0;text-align:center;font-size:13px;line-height:22px;color:var(--muted)}

.features{padding-top:100px;height:1024px - 0px}
.feature-row{display:flex;justify-content:space-between;width:1000px;margin:68px auto 0}
.feature{width:300px;display:flex;gap:16px}
.feature svg{flex:none;margin-top:2px}
.feature h3{font-size:14px;font-weight:700;color:var(--accent);letter-spacing:.5px}
.feature p{font-size:12px;line-height:19px;color:var(--muted);margin-top:8px}
.feature .more{display:block;font-size:12px;color:var(--accent);margin-top:10px;font-weight:600}

.listings{position:absolute;top:1160px;left:0;width:1200px;height:410px;background:var(--grey-bg);padding-top:110px}
.listings .section-title{margin-top:-10px}
.cards{display:flex;justify-content:space-between;width:1000px;margin:44px auto 0}
.card{width:232px}
.card-photo{height:132px}
.p1{background:linear-gradient(180deg,#6fb6e6,#2b7fb8 60%,#1e5f86)}
.p2{background:linear-gradient(180deg,#dfe7ef,#a8b9c8)}
.p3{background:linear-gradient(135deg,#e4c9a6,#8f6f55)}
.p4{background:linear-gradient(180deg,#7ec1e8,#2f8fc2 65%,#2a6d3c)}
.card h4{font-size:12px;font-weight:700;color:var(--accent);margin-top:12px}
.card p{font-size:11px;line-height:16px;color:var(--muted);margin-top:4px}
.rating{display:flex;align-items:center;gap:2px;margin-top:6px;font-size:11px;color:var(--muted)}
.rating i{color:var(--orange);font-style:normal;font-size:13px}

.feedback{position:absolute;top:1570px;left:0;width:1200px;text-align:center;padding-top:30px}
.avatar{width:66px;height:66px;border-radius:50%;background:linear-gradient(180deg,#b9c2cc,#7d8894);margin:34px auto 0;border:3px solid var(--white);box-shadow:0 0 0 1px var(--line)}
.person{font-size:12px;font-weight:700;color:var(--accent);margin-top:10px;letter-spacing:1px}

.bottom{position:absolute;top:1900px;left:0;width:1200px;height:320px;background:#f6f7f8;border-top:1px solid var(--line);display:flex;gap:44px;padding:32px 96px 0}
.col h5{font-family:'Roboto Condensed',Arial,sans-serif;font-size:22px;font-weight:700;color:var(--navy);display:flex;align-items:center;gap:10px;letter-spacing:.5px}
.col h5 b{color:var(--orange)}
.col-dest{width:300px}
.dest-lists{display:flex;gap:40px;margin-top:18px}
.dest-lists ul{list-style:none;font-size:11px;line-height:24px;color:var(--text);text-transform:uppercase;width:120px}
.col-crowds{width:330px}
.crowds-body{display:flex;gap:18px;margin-top:18px}
.crowds-photo{width:140px;height:96px;background:linear-gradient(180deg,#7cc0e6,#2f86b9 60%,#f1e1b8)}
.crowds-body ul{list-style:none;font-size:11px;line-height:22px;text-transform:uppercase}
.col-pick{width:300px}
.col-pick p{font-size:12px;line-height:20px;color:var(--muted);margin-top:18px}

.footer{position:absolute;top:2220px;left:0;width:1200px;height:108px;background:var(--footer);display:flex;align-items:center;justify-content:space-between;padding:0 96px;color:#aeb6bf}
.footer-links{font-size:12px;font-weight:600;letter-spacing:1px;color:#d5dbe1}
.footer-links span{margin:0 8px;color:#6b7580}
.copy{font-size:11px;margin-top:10px}
.connect{display:flex;align-items:center;gap:10px;font-size:13px;font-weight:600;color:#d5dbe1;letter-spacing:1px}
.connect .social span{width:30px;height:30px}
</style>
</head>
<body>

<header class="topbar">
  <div class="brand"><span class="brand-mark"></span>CALDERA KEY</div>
  <div class="top-tools">
    <div class="lang">Select Language <span class="lang-box"></span></div>
    <div class="social"><span class="s1"></span><span class="s2"></span><span class="s3"></span><span class="s4"></span></div>
  </div>
</header>

<nav class="mainnav">
  <a class="active" href="#">HOME</a>
  <a href="#">ABOUT US</a>
  <a href="#">SERVICES</a>
  <a href="#">BLOG</a>
  <a href="#">CONTACT US</a>
  <a href="#">LOGIN</a>
  <a href="#">REGISTER</a>
</nav>

<section class="hero">
  <div class="hero-photo" role="img" aria-label="Two hikers with backpacks walking on a ridge at sunset"></div>
  <div class="palm-left" role="img" aria-label="Palm leaves framing the left edge"></div>
  <div class="palm-right" role="img" aria-label="Palm leaves framing the right edge"></div>
  <div class="hero-content">
    <h1 class="hero-title">AT VERO EOS ET ACCUSAMUS</h1>
    <p class="hero-sub">Nam libero tempore cum soluta nobis est eligendi optio cumque nihil impedit quo minus id quod</p>
    <a class="btn" href="#">READ MORE</a>
  </div>
  <div class="dots"><span class="on"></span><span></span><span></span><span></span></div>
</section>

<section class="features">
  <h2 class="section-title">CALDERA KEY FEATURES</h2>
  <div class="section-rule"></div>
  <p class="intro">At vero eos et accusamus et iusto odio dignissimos ducimus qui blanditiis praesentium voluptatum deleniti atque corrupti quos dolores et quas molestias excepturi sint occaecati cupiditate non provident, similique sunt in culpa qui officia deserunt mollitia animi, id est laborum et dolorum fuga. Et harum quidem rerum facilis est et expedita distinctio nam libero tempore.</p>
  <div class="feature-row">
    <div class="feature">
      <svg width="22" height="22" viewBox="0 0 24 24"><path d="M2 13l20-9-6 18-4-7-7-2z" fill="var(--accent)"/></svg>
      <div>
        <h3>SELLING GUIDED TOURS</h3>
        <p>Nam libero tempore cum soluta nobis est eligendi optio cumque nihil impedit quo minus id quod maxime placeat.</p>
        <a class="more" href="#">Read More »</a>
      </div>
    </div>
    <div class="feature">
      <svg width="22" height="22" viewBox="0 0 24 24"><rect x="3" y="10" width="18" height="8" fill="var(--accent)"/><rect x="3" y="6" width="7" height="5" fill="var(--accent)"/><rect x="2" y="18" width="2" height="3" fill="var(--accent)"/><rect x="20" y="18" width="2" height="3" fill="var(--accent)"/></svg>
      <div>
        <h3>HOTEL HOSTELS</h3>
        <p>Temporibus autem quibusdam et aut officiis debitis aut rerum necessitatibus saepe eveniet ut et voluptates.</p>
        <a class="more" href="#">Read More »</a>
      </div>
    </div>
    <div class="feature">
      <svg width="22" height="22" viewBox="0 0 24 24"><circle cx="12" cy="12" r="7" fill="none" stroke="var(--accent)" stroke-width="4" stroke-dasharray="4 2.5"/><circle cx="12" cy="12" r="3" fill="var(--accent)"/></svg>
      <div>
        <h3>RENTAL VEHICLES</h3>
        <p>Itaque earum rerum hic tenetur a sapiente delectus ut aut reiciendis voluptatibus maiores alias consequatur aut.</p>
        <a class="more" href="#">Read More »</a>
      </div>
    </div>
  </div>
</section>

<section class="listings">
  <h2 class="section-title">OUR LISTINGS</h2>
  <div class="section-rule"></div>
  <div class="cards">
    <article class="card">
      <div class="card-photo p1" role="img" aria-label="Boats on a clear blue lake"></div>
      <h4>EAST COAST LAKE FISHING</h4>
      <p>Simply dummy text of the printing and typesetting industry.</p>
      <div class="rating"><i>★★★★</i><i style="color:#c9ced3">★</i>&nbsp;999 Reviews</div>
    </article>
    <article class="card">
      <div class="card-photo p2" role="img" aria-label="Pale sky over an open landscape"></div>
      <h4>ADVENTURES IN AFRICA</h4>
      <p>Simply dummy text of the printing and typesetting industry.</p>
      <div class="rating"><i>★★★★</i><i style="color:#c9ced3">★</i>&nbsp;999 Reviews</div>
    </article>
    <article class="card">
      <div class="card-photo p3" role="img" aria-label="Group of friends on an island outing"></div>
      <h4>ISLAND CALLING</h4>
      <p>Simply dummy text of the printing and typesetting industry.</p>
      <div class="rating"><i>★★★★</i><i style="color:#c9ced3">★</i>&nbsp;999 Reviews</div>
    </article>
    <article class="card">
      <div class="card-photo p4" role="img" aria-label="Lake shore with trees under blue sky"></div>
      <h4>EAST COAST LAKE FISHING</h4>
      <p>Simply dummy text of the printing and typesetting industry.</p>
      <div class="rating"><i>★★★★</i><i style="color:#c9ced3">★</i>&nbsp;999 Reviews</div>
    </article>
  </div>
</section>

<section class="feedback">
  <h2 class="section-title">CUSTOMER FEEDBACK</h2>
  <div class="section-rule"></div>
  <p class="intro">Lorem ipsum dolor sit amet, consectetur adipiscing elit, sed do eiusmod tempor incididunt ut labore et dolore magna aliqua. Ut enim ad minim veniam, quis nostrud exercitation ullamco laboris nisi ut aliquip ex ea commodo consequat duis aute irure dolor.</p>
  <div class="avatar" role="img" aria-label="Customer portrait"></div>
  <div class="person">TOMAS REYNE</div>
</section>

<section class="bottom">
  <div class="col col-dest">
    <h5><svg width="18" height="22" viewBox="0 0 18 22"><path d="M9 0a8 8 0 0 1 8 8c0 6-8 14-8 14S1 14 1 8a8 8 0 0 1 8-8z" fill="var(--orange)"/><circle cx="9" cy="8" r="3" fill="#fff"/></svg>HOT <b>DESTINATIONS</b></h5>
    <div class="dest-lists">
      <ul><li>Rome</li><li>San Diego</li><li>Miami</li><li>New York City</li><li>London</li><li>Amsterdam</li><li>Barcelona</li></ul>
      <ul><li>Budapest</li><li>Venice</li><li>Beijing</li><li>San Francisco</li><li>Tokyo</li><li>Las Vegas</li><li>Sydney</li></ul>
    </div>
  </div>
  <div class="col col-crowds">
    <h5><svg width="20" height="20" viewBox="0 0 20 20"><circle cx="10" cy="10" r="9" fill="var(--orange)"/><path d="M5 10l3 3 7-7" stroke="#fff" stroke-width="2.4" fill="none"/></svg><b>BEAT THE CROWDS</b> IN EUROPE</h5>
    <div class="crowds-body">
      <div class="crowds-photo" role="img" aria-label="Coastal town by the sea"></div>
      <ul><li>Paris Tours</li><li>Rome Tours</li><li>London Tours</li><li>Venice Tours</li><li>Madrid Tours</li></ul>
    </div>
  </div>
  <div class="col col-pick">
    <h5><svg width="20" height="20" viewBox="0 0 20 20"><rect x="1" y="3" width="18" height="16" rx="2" fill="var(--orange)"/><rect x="1" y="3" width="18" height="4" fill="#d47d0c"/></svg><b>OCTOBER</b> INSIDER'S PICK</h5>
    <p>Sed ut perspiciatis unde omnis iste natus error sit voluptatem accusantium doloremque laudantium, totam rem aperiam eaque ipsa quae ab illo inventore veritatis et quasi architecto beatae vitae dicta sunt explicabo. Nemo enim ipsam voluptatem quia voluptas sit aspernatur aut odit aut fugit.</p>
  </div>
</section>

<footer class="footer">
  <div>
    <div class="footer-links">HOME<span>|</span>ABOUT US<span>|</span>SERVICES<span>|</span>BLOG<span>|</span>CONTACT US<span>|</span>LOGIN</div>
    <div class="copy">Copyright © 2015 Caldera Key. All Rights Reserved</div>
  </div>
  <div class="connect">CONNECT US
    <div class="social"><span class="s1"></span><span class="s2"></span><span class="s3"></span><span class="s4"></span><span class="s5"></span></div>
  </div>
</footer>

</body>
</html>
```